HARBORLINE AUTO GLASS

Mobile Glass Shop:

1) Windshield REPAIR 2)Windshield replacment 3) Rear Windshield Replacment 4) Side Window Replacment 5) car window replacment 6) Power Window Repair.

Schedual a service within 24 hour with one of our certified technicians.
Updates

See "brightvane auto repair" web site for referance on the nature of our buisness and service. www.brightvane-example.com

Coding

```html
<!DOCTYPE html>
<html lang="en">
<head>
<meta charset="utf-8">
<title>Harborline Auto Glass</title>
<link href="https://fonts.googleapis.com/css2?family=Poppins:wght@400;500;600;700&display=swap" rel="stylesheet">
<style>
:root{
  --blue:#1a7fc1;
  --blue-dark:#0f65a3;
  --btn:#5ba4da;
  --ink:#333333;
  --text:#555555;
  --footer:#373737;
  --gray-band:#efefef;
  --white:#ffffff;
}
*{box-sizing:border-box;margin:0;padding:0}
html,body{width:1200px;height:4104px;overflow:hidden}
body{font-family:'Poppins',sans-serif;color:var(--ink);background:var(--white);position:relative}
.abs{position:absolute}
.brand{display:flex;align-items:center;gap:10px;font-weight:700;color:var(--blue);font-size:22px;letter-spacing:.5px;line-height:1.15}
.brand-mark{width:34px;height:34px;background:var(--blue);flex:none}
.header-phone{left:828px;top:32px;display:flex;align-items:center;gap:20px;font-size:28px;font-weight:600;color:var(--blue)}
.phone-circle{width:46px;height:46px;border-radius:50%;background:#2f2f2f;display:flex;align-items:center;justify-content:center}
.nav{left:0;top:112px;width:1200px;height:57px;background:linear-gradient(90deg,#2c8fd0,#1375b8)}
.nav ul{list-style:none;display:flex;gap:42px;position:absolute;left:74px;top:20px}
.nav li{color:var(--white);font-size:14px;font-weight:600;text-transform:uppercase}
.nav-cta{right:0;top:0;width:345px;height:57px;background:#4a4a4a;clip-path:polygon(30px 0,100% 0,100% 100%,0 100%);color:var(--white);font-size:15px;font-weight:600;display:flex;align-items:center;justify-content:flex-end;padding-right:74px;gap:14px}
.hero{left:0;top:169px;width:1200px;height:577px;background:linear-gradient(100deg,#bdbdbd 0%,#8a8a8a 35%,#6f7478 60%,#a2a6a8 100%)}
.hero-title{left:75px;top:330px;color:var(--white);font-weight:700;line-height:1.2}
.hero-title .small{font-size:40px}
.hero-title .big{font-size:48px}
.hero-tag{left:75px;top:446px;color:var(--white);font-size:29px;font-weight:600}
.btn{background:var(--btn);color:var(--white);font-weight:600;font-size:18px;display:flex;align-items:center;justify-content:center;text-transform:uppercase}
.dots{display:flex;gap:14px}
.dot{width:13px;height:13px;border-radius:50%;background:var(--white)}
.dot.on{background:var(--blue)}
.dots.dark .dot{background:#555}
.dots.dark .dot.on{background:var(--blue)}
.section-title{left:0;width:1200px;text-align:center;font-size:38px;font-weight:700;color:#3a3a3a}
.card{width:328px;height:265px;border-radius:8px;overflow:hidden;background:linear-gradient(135deg,#9aa4ab,#4d565d)}
.card-label{position:absolute;left:0;bottom:0;width:248px;height:68px;background:var(--white);border-top-right-radius:66px;padding:8px 0 0 15px;color:var(--blue);font-weight:700;font-size:21px;line-height:29px;text-transform:uppercase}
.about-band{left:0;top:1578px;width:1200px;height:526px;background:linear-gradient(90deg,#5ba8dc 0%,#2f86c6 50%,#0e5f9f 100%)}
.about-photo{left:617px;top:1602px;width:508px;height:558px;background:linear-gradient(135deg,#c7ccd0,#a8b0b5 40%,#c44a4f 75%,#888 100%);clip-path:polygon(0 0,100% 0,100% 100%,0 100%,20px 50%)}
.about-heading{left:75px;top:1644px;color:var(--white);font-size:38px;font-weight:700;line-height:44px}
.about-text{left:75px;top:1752px;width:510px;color:var(--white);font-size:14px;line-height:29.5px}
.btn-outline{left:75px;top:1962px;width:178px;height:54px;border:2px solid var(--white);color:var(--white);font-weight:600;font-size:17px;display:flex;align-items:center;justify-content:center}
.why{width:328px;height:346px;border:2px solid #dadada;text-align:center}
.why-icon{width:94px;height:94px;border-radius:50%;background:var(--blue);margin:26px auto 0;display:flex;align-items:center;justify-content:center}
.why h3{color:var(--blue);font-size:18px;font-weight:600;margin-top:24px;text-transform:uppercase}
.why p{font-size:14px;line-height:26px;color:var(--text);margin:8px 30px 0}
.btn-pill{margin:16px auto 0;width:152px;height:42px;border-radius:21px;background:#3c3c3c;color:var(--white);font-size:13px;font-weight:600;display:flex;align-items:center;justify-content:center}
.schedule-band{left:0;top:2748px;width:1200px;height:420px;background:var(--gray-band)}
.schedule-photo{left:590px;top:2718px;width:598px;height:450px;background:linear-gradient(180deg,#41475a,#2d3142);clip-path:polygon(10% 6%,90% 0,100% 30%,96% 100%,10% 100%,0 30%)}
.schedule-heading{left:74px;top:2858px;font-size:48px;font-weight:700;line-height:56px;color:#3a3a3a}
.schedule-heading span{color:var(--blue)}
.rating{left:0;top:3300px;width:1200px;display:flex;justify-content:center;align-items:center;gap:10px;font-size:20px;color:#3a3a3a}
.avatar{position:absolute;width:92px;height:92px;border-radius:50%;background:linear-gradient(135deg,#b88a6a,#6d4d3a)}
.review-text{position:absolute;font-size:15px;line-height:29.5px;color:var(--text)}
.review-name{position:absolute;font-size:17px;font-weight:600;color:var(--blue)}
.footer{left:0;top:3709px;width:1200px;height:395px;background:var(--footer);color:#e5e5e5}
.footer h4{font-size:16px;font-weight:600;color:var(--white);margin-bottom:12px}
.footer li{list-style:none;font-size:15px;line-height:36px}
.footer .copy{font-size:14px;line-height:22px}
.footer-brand{color:var(--white);font-size:22px;width:240px}
.addr li{display:flex;gap:20px;align-items:flex-start;line-height:27px;margin-bottom:11px}
.addr svg{flex:none;margin-top:6px}
.social{display:flex;gap:22px}
.social span{width:22px;height:22px;border-radius:50%;background:var(--white)}
</style>
</head>
<body>

<header>
  <div class="abs brand" style="left:75px;top:38px"><span class="brand-mark"></span>HARBORLINE AUTO GLASS</div>
  <div class="abs header-phone">
    <span class="phone-circle"><svg width="22" height="22" viewBox="0 0 24 24"><path fill="#fff" d="M6.6 10.8a15 15 0 0 0 6.6 6.6l2.2-2.2c.3-.3.7-.4 1-.2 1.1.4 2.3.6 3.6.6.6 0 1 .4 1 1V20c0 .6-.4 1-1 1A17 17 0 0 1 3 4c0-.6.4-1 1-1h3.5c.6 0 1 .4 1 1 0 1.3.2 2.5.6 3.6.1.3 0 .7-.2 1z"/></svg></span>
    1-800-555-0142
  </div>
</header>

<nav class="abs nav">
  <ul><li>Home</li><li>About Us</li><li>Services</li><li>Testimonials</li><li>Gallery</li><li>Contact Us</li></ul>
  <div class="abs nav-cta">
    <svg width="16" height="16" viewBox="0 0 16 16"><rect x="1.5" y="3" width="13" height="11.5" fill="none" stroke="#fff" stroke-width="1.5"/><path d="M1.5 6.5h13M5 1v4M11 1v4" stroke="#fff" stroke-width="1.5"/></svg>
    SCHEDULE A SERVICE
  </div>
</nav>

<section>
  <div class="abs hero" role="img" aria-label="Technician fitting a new windshield onto a car in a workshop"></div>
  <div class="abs hero-title"><div class="small">WELCOME TO</div><div class="big">HARBORLINE AUTO GLASS</div></div>
  <div class="abs hero-tag">Broken glass? We'll fix it fast.</div>
  <div class="abs btn" style="left:75px;top:518px;width:200px;height:54px">Schedule Now</div>
  <div class="abs dots" style="left:554px;top:692px"><span class="dot on"></span><span class="dot"></span><span class="dot"></span><span class="dot"></span></div>
</section>

<section>
  <h2 class="abs section-title" style="top:814px">OUR SERVICES</h2>
  <div class="abs card" style="left:75px;top:899px" role="img" aria-label="Technician repairing a windshield"><div class="card-label">Windshield<br>Repair</div></div>
  <div class="abs card" style="left:434px;top:899px" role="img" aria-label="Two technicians lifting a windshield"><div class="card-label">Windshield<br>Replacment</div></div>
  <div class="abs card" style="left:797px;top:899px" role="img" aria-label="Rear windshield being fitted"><div class="card-label">Rear Windshield<br>Replacment</div></div>
  <div class="abs card" style="left:75px;top:1213px" role="img" aria-label="Side window glass being installed"><div class="card-label">Side Window<br>Replacment</div></div>
  <div class="abs card" style="left:434px;top:1213px" role="img" aria-label="Car window replacement in progress"><div class="card-label">Car Window<br>Replacment</div></div>
  <div class="abs card" style="left:797px;top:1213px" role="img" aria-label="Finger pressing power window switch"><div class="card-label">Power Window<br>Repair.</div></div>
</section>

<section>
  <div class="abs about-band"></div>
  <div class="abs about-photo" role="img" aria-label="Technician holding a windshield with suction cups"></div>
  <h2 class="abs about-heading">ABOUT HARBORLINE<br>AUTO GLASS</h2>
  <p class="abs about-text">Sed ut perspiciatis unde omnis iste natus error sit voluptatem accusantium doloremque laudantium, totam rem aperiam, eaque ipsa quae ab illo inventore veritatis et quasi architecto beatae vitae dicta sunt explicabo. Nemo enim ipsam voluptatem quia voluptas sit aspernatur aut odit aut fugit, sed quia consequuntur magni dolores eos qui ratione voluptatem sequi nesciunt.</p>
  <div class="abs btn-outline">READ MORE</div>
</section>

<section>
  <h2 class="abs section-title" style="top:2210px">WHY CHOOSE US</h2>
  <div class="abs why" style="left:75px;top:2300px">
    <div class="why-icon"><svg width="30" height="36" viewBox="0 0 30 36"><path fill="#fff" d="M2 0h18l8 8v28H2z"/><path d="M8 16h14M8 21h14M8 26h14" stroke="#1a7fc1" stroke-width="2"/></svg></div>
    <h3>Stress-Free Claims</h3>
    <p>Sed ut perspiciatis unde omnis iste natus error sit voluptatem accusanti um doloremque</p>
    <div class="btn-pill">LEARN MORE</div>
  </div>
  <div class="abs why" style="left:436px;top:2300px">
    <div class="why-icon"><svg width="42" height="32" viewBox="0 0 42 32"><path fill="#fff" d="M0 4l13-4v28L0 32zM15 0l12 4v28l-12-4zM29 4l13-4v28l-13 4z"/></svg></div>
    <h3>Shops Near You</h3>
    <p>Sed ut perspiciatis unde omnis iste natus error sit voluptatem accusanti um doloremque</p>
    <div class="btn-pill">LEARN MORE</div>
  </div>
  <div class="abs why" style="left:797px;top:2300px">
    <div class="why-icon"><svg width="38" height="38" viewBox="0 0 38 38"><path fill="#fff" d="M26 2a9 9 0 0 0-9 12L2 29l7 7 15-15a9 9 0 0 0 12-9l-6 5-5-1-1-5 6-6z"/></svg></div>
    <h3>Superior Repairs</h3>
    <p>Sed ut perspiciatis unde omnis iste natus error sit voluptatem accusanti um doloremque</p>
    <div class="btn-pill">LEARN MORE</div>
  </div>
</section>

<section>
  <div class="abs schedule-band"></div>
  <div class="abs schedule-photo" role="img" aria-label="Three smiling technicians in dark overalls holding clipboards"></div>
  <h2 class="abs schedule-heading">SCHEDULE A SERVICE<br>WITHIN <span>24 HOUR</span></h2>
  <div class="abs btn" style="left:75px;top:2992px;width:200px;height:54px">Schedule Now</div>
</section>

<section>
  <h2 class="abs section-title" style="top:3228px">REAL CUSTOMER REVIEWS</h2>
  <div class="abs rating">Customers rate Brightvane
    <svg width="150" height="22" viewBox="0 0 150 22"><g fill="#f7941d"><path id="st" d="M11 0l3.2 7 7.6.7-5.8 5 1.8 7.5L11 16.3 4.2 20.2 6 12.7 0.2 7.7 7.8 7z"/><use href="#st" x="30"/><use href="#st" x="60"/><use href="#st" x="90"/><use href="#st" x="120"/></g></svg>
    4.67 out of 5</div>
  <div class="avatar" style="left:75px;top:3379px" role="img" aria-label="Customer portrait"></div>
  <p class="review-text" style="left:188px;top:3370px;width:410px">"&nbsp; Sed ut perspiciatis unde omnis iste natus error sit voluptatem accusantium doloremque laudantium, totam rem aperiam, eaque ipsa quae ab illo inventore veritatis et quasi architecto beatae vitae dicta sunt explicabo.."</p>
  <div class="review-name" style="left:188px;top:3530px">Name Heading</div>
  <div class="avatar" style="left:618px;top:3379px" role="img" aria-label="Customer couple portrait"></div>
  <p class="review-text" style="left:732px;top:3370px;width:410px">"&nbsp; Sed ut perspiciatis unde omnis iste natus error sit voluptatem accusantium doloremque laudantium, totam rem aperiam, eaque ipsa quae ab illo inventore veritatis et quasi architecto beatae vitae dicta sunt explicabo.."</p>
  <div class="review-name" style="left:732px;top:3530px">Name Heading</div>
  <div class="abs dots dark" style="left:554px;top:3614px"><span class="dot on"></span><span class="dot"></span><span class="dot"></span><span class="dot"></span></div>
</section>

<footer class="abs footer">
  <div class="abs brand footer-brand" style="left:75px;top:98px"><span class="brand-mark"></span><span>HARBORLINE<br>AUTO GLASS</span></div>
  <p class="abs copy" style="left:75px;top:213px">Copyright© 2022 Company Name<br>All Right Reserved</p>
  <div class="abs social" style="left:75px;top:283px"><span></span><span></span><span></span><span></span><span></span></div>
  <div class="abs" style="left:373px;top:76px"><h4>OUR COMPANY</h4><ul><li>Home</li><li>About Us</li><li>Services</li><li>Testimonials</li><li>Gallery</li><li>Contact Us</li></ul></div>
  <div class="abs" style="left:588px;top:76px"><h4>SERVICES</h4><ul><li>Windshield Repair</li><li>Windshield Replacement</li><li>Rear Windshield Replacement</li><li>Side Window Replacement</li><li>Car Window Replacement</li><li>Power Window Repair</li></ul></div>
  <div class="abs addr" style="left:883px;top:76px;width:260px"><h4>ADDRESS</h4><ul>
    <li><svg width="16" height="14" viewBox="0 0 16 14"><path fill="#5ba4da" d="M0 2l5-2 6 2 5-2v12l-5 2-6-2-5 2z"/></svg>Excepteur sintcaecat cupid ataton proident</li>
    <li><svg width="16" height="16" viewBox="0 0 24 24"><path fill="#5ba4da" d="M6.6 10.8a15 15 0 0 0 6.6 6.6l2.2-2.2c.3-.3.7-.4 1-.2 1.1.4 2.3.6 3.6.6.6 0 1 .4 1 1V20c0 .6-.4 1-1 1A17 17 0 0 1 3 4c0-.6.4-1 1-1h3.5c.6 0 1 .4 1 1 0 1.3.2 2.5.6 3.6.1.3 0 .7-.2 1z"/></svg>1-800-555-0142</li>
    <li><svg width="16" height="12" viewBox="0 0 16 12"><rect width="16" height="12" fill="#5ba4da"/><path d="M0 0l8 6 8-6" stroke="#373737" fill="none"/></svg>info@companyname.com</li>
    <li><svg width="14" height="18" viewBox="0 0 14 18"><path fill="#5ba4da" d="M7 0a7 7 0 0 1 7 7c0 5-7 11-7 11S0 12 0 7a7 7 0 0 1 7-7zm0 4a3 3 0 1 0 0 6 3 3 0 0 0 0-6z"/></svg><span style="color:#5ba4da">Map Direction</span></li>
  </ul></div>
</footer>

</body>
</html>
```